Corvana Tongue Works, LLC

We need a business card that includes information about our business and conveys a reliable business that provides document translation services and interpreters for a variety of corporate and individual clients. We want to come across as professional, reliable, yet approachable. It should include the following on one side:

ESL / ENL Language Classes, Private Lessons, and Online Tutors
PLEXA Training and Testing
Translating & Interpreting Services
Contact us about Over-the-Phone Interpreting in over 200 languages
24/7/365
www.corvanatongue.example

The other side should include (555) 481-3062

Rhoda Pelling, President
482 Garnet Ave., Ste. 219
Indianapolis, IN 40917

Please add USA as part of the address. Also, please add rmpelling@corvanatongueworks.example as the e-mail address. Thank you.

Target Market(s)

Business professionals, their families, the international community

Industry/Entity Type

Business

Contact Information for Business Card

24/7/365
www.corvanatongue.example

(555) 481-3062

Rhoda Pelling, President
482 Garnet Ave., Ste. 219
Indianapolis, IN 40917
USA

Font styles to use
Sans Serif

Colors

Designer to choose colors to be used in the design.

Requirements
Must have
• See project description
• e-mail address and web address
• Phone number
Nice to have
• a globe
• physical address
Should not have
• Should not have the same color scheme as other agencies in our market in Indiana unless it is blue and black. No purple or yellow.

```html
<!DOCTYPE html>
<html lang="en">
<head>
<meta charset="utf-8">
<title>Corvana Tongue Works, LLC — Business Card</title>
<link rel="stylesheet" href="https://fonts.googleapis.com/css2?family=Open+Sans:wght@400;600&display=swap">
<style>
  :root {
    --bg: #e4e4e4;
    --charcoal: #2e3032;
    --map-tone: #3a3d40;
    --blue: #1a95d2;
    --ink: #2a2a2a;
    --white: #ffffff;
  }
  * { box-sizing: border-box; margin: 0; padding: 0; }
  html, body {
    width: 1200px; height: 852px; overflow: hidden;
    background: var(--bg);
    font-family: "Open Sans", Arial, sans-serif;
  }
  .stage { position: relative; width: 1200px; height: 852px; }
  .card {
    position: absolute; top: 271px;
    width: 540px; height: 310px;
    border-radius: 22px; overflow: hidden;
  }
  /* ---------- back side ---------- */
  .card--back { left: 40px; background: var(--charcoal); color: var(--white); }
  .back__map {
    position: absolute; left: 40px; top: 34px; width: 460px; height: 210px;
    border-radius: 40% 50% 45% 40%;
    background: radial-gradient(ellipse at center, var(--map-tone) 0%, var(--charcoal) 72%);
  }
  .back__content { position: absolute; inset: 0; text-align: center; padding-top: 44px; }
  .services { list-style: none; font-size: 15px; line-height: 22px; }
  .services .chev { color: var(--blue); margin: 0 5px; }
  .back__rule { width: 240px; height: 1px; background: var(--blue); margin: 12px auto 10px; }
  .back__contact { font-size: 15px; line-height: 22px; }
  .back__web {
    position: absolute; left: 0; right: 0; bottom: 28px;
    font-size: 14px; text-align: center;
  }
  .accent { color: var(--blue); }

  /* ---------- front side ---------- */
  .card--front { left: 620px; background: var(--white); color: var(--ink); }
  .front__waves { position: absolute; inset: 0; }
  .taglines {
    position: absolute; right: 26px; top: 16px;
    list-style: none; text-align: right;
    color: var(--white); font-size: 13px; line-height: 19px;
  }
  .brand {
    position: absolute; right: 24px; top: 140px;
    display: flex; align-items: center; gap: 12px;
  }
  .brand__dot {
    width: 78px; height: 78px; border-radius: 50%;
    background: var(--blue); flex: none;
  }
  .brand__name { font-size: 21px; line-height: 23px; font-weight: 600; color: var(--ink); }
  .person { position: absolute; left: 30px; top: 132px; }
  .person__name { font-size: 20px; font-weight: 600; color: var(--blue); line-height: 24px; }
  .person__title { font-size: 11.5px; margin-left: 14px; line-height: 16px; }
  .details {
    position: absolute; left: 30px; top: 190px;
    font-size: 12.5px; line-height: 17px;
  }
  .details__address { margin-left: 16px; margin-bottom: 6px; }
  .contact-list { list-style: none; }
  .contact-list li { display: flex; align-items: center; gap: 8px; }
  .contact-list svg { width: 10px; height: 10px; flex: none; }
</style>
</head>
<body>
<main class="stage">

  <!-- Back side -->
  <section class="card card--back" aria-label="Card back: services">
    <div class="back__map" role="img" aria-label="Faint world map in the background"></div>
    <div class="back__content">
      <ul class="services">
        <li><span class="chev">»</span>ESL / ENL Language Classes</li>
        <li><span class="chev">»</span>Private Lessons <span class="chev">»</span>Online Tutors</li>
        <li><span class="chev">»</span>PLEXA Training and Testing</li>
        <li><span class="chev">»</span>Translating &amp; Interpreting Services</li>
      </ul>
      <div class="back__rule"></div>
      <p class="back__contact">Contact us about Over-the-Phone<br>Interpreting in over 200 languages<br>24/7/365</p>
    </div>
    <p class="back__web">www.<span class="accent">corvanatongue</span>.example</p>
  </section>

  <!-- Front side -->
  <section class="card card--front" aria-label="Card front: contact details">
    <svg class="front__waves" viewBox="0 0 540 310" aria-hidden="true">
      <path d="M0,0 H540 V85 C450,85 380,80 300,98 C200,120 100,55 0,72 Z" fill="#1a95d2"/>
      <path d="M540,94 C450,94 380,89 300,107 C200,129 100,64 0,81" fill="none" stroke="#2a2a2a" stroke-width="6"/>
      <path d="M540,104 C460,106 390,104 310,124" fill="none" stroke="#2a2a2a" stroke-width="2"/>
    </svg>

    <ul class="taglines">
      <li>Language Training «</li>
      <li>Interpreting «</li>
      <li>Translating «</li>
    </ul>

    <div class="brand">
      <span class="brand__dot"></span>
      <p class="brand__name">Corvana<br>Tongue Works<br>LLC</p>
    </div>

    <div class="person">
      <p class="person__name">Rhoda Pelling</p>
      <p class="person__title">President</p>
    </div>

    <div class="details">
      <p class="details__address">482 Garnet Ave., Ste. 219<br>Indianapolis, IN 40917 US</p>
      <ul class="contact-list">
        <li>
          <svg viewBox="0 0 10 10"><path d="M2,1 L4,1 L4.5,3 L3.3,3.8 C3.9,5.2 4.8,6.1 6.2,6.7 L7,5.5 L9,6 L9,8 C5,8.5 1.5,5 2,1 Z" fill="#1a95d2"/></svg>
          <span>(555) 481-3062</span>
        </li>
        <li>
          <svg viewBox="0 0 10 10"><rect x="0.5" y="2" width="9" height="6" fill="#1a95d2"/><path d="M0.5,2 L5,5.5 L9.5,2" fill="none" stroke="#fff" stroke-width="0.8"/></svg>
          <span>rmpelling@corvanatongueworks.example</span>
        </li>
        <li>
          <svg viewBox="0 0 10 10"><circle cx="5" cy="5" r="4.3" fill="none" stroke="#1a95d2" stroke-width="1.2"/><path d="M0.7,5 H9.3 M5,0.7 V9.3" stroke="#1a95d2" stroke-width="1"/></svg>
          <span class="accent">corvanatongue.example</span>
        </li>
      </ul>
    </div>
  </section>

</main>
</body>
</html>
```